A start-up named "lumerova" - a clinical research organization needs a new PowerPoint design

We need a new PowerPoint Design (incl. business card and stationery design) for an early-stage start-up named "lumerova" seeking to build an ecosystem/ strategic partner alliances or consortium of committed and active collaborators to guide important components of the clinical trial.

Our ultimate goal is to avoid false neutrals – therapies that have not been and may never be evaluated in clinical trials due to the costs and/ or complexity.

The final design should highlight our patient-centric approach, innovative study design supported with the novel AI platform to make a stronger impact on patient lives.

Please see the attached brief for more details.
Updates

Requesting the proposals on color-coding, business-card designs, clinical research visuals, and icons as well as stationery design.

Target Market(s)

Pharma/ Biotech Executives
Medical Institutions
Clinical Trial Participants (Patients)

Colors
e34398

Requirements
Must have
• Use the Color Version of purple/ magenta logo

```html
<!DOCTYPE html>
<html lang="en">
<head>
<meta charset="utf-8">
<title>lumerova – business cards</title>
<link rel="stylesheet" href="https://fonts.googleapis.com/css2?family=Montserrat:wght@400;500;600;700&display=swap">
<style>
  :root {
    --magenta: #c8157a;
    --magenta-deep: #a92a6e;
    --magenta-bright: #d81b84;
    --accent-orange: #e8603c;
    --ink: #222226;
    --paper: #ffffff;
    --backdrop-top: #e4e7ec;
    --backdrop-bottom: #c8cfd8;
  }
  * { box-sizing: border-box; margin: 0; padding: 0; }
  html, body { width: 1200px; height: 675px; overflow: hidden; }
  body {
    position: relative;
    background: linear-gradient(160deg, var(--backdrop-top), var(--backdrop-bottom));
    font-family: "Montserrat", sans-serif;
    color: var(--ink);
  }
  .card {
    position: absolute;
    background: var(--paper);
    box-shadow: 0 10px 26px rgba(40, 50, 70, 0.18);
    overflow: hidden;
  }

  /* Front card */
  .card-front { left: 100px; top: 188px; width: 525px; height: 300px; }
  .brand {
    position: absolute; left: 0; right: 0; top: 84px;
    text-align: center;
  }
  .brand-name {
    font-weight: 700; font-size: 38px; letter-spacing: -0.5px;
    color: var(--magenta-deep); line-height: 1;
  }
  .contact-band { position: absolute; left: 0; top: 178px; width: 525px; height: 44px; }
  .band-text {
    position: absolute; top: 191px; color: #fff;
    font-size: 14px; font-weight: 500; letter-spacing: 0.6px;
  }
  .band-web { left: 118px; }
  .band-phone { left: 352px; }

  /* Back card */
  .card-back { left: 700px; top: 75px; width: 300px; height: 525px; }
  .back-art { position: absolute; left: 0; top: 0; }
  .back-brand { position: absolute; left: 34px; top: 62px; }
  .back-brand .brand-name { color: #fff; font-size: 30px; }
  .portrait {
    position: absolute; left: 162px; top: 128px; width: 88px; height: 88px;
    border-radius: 50%; border: 4px solid #fff;
    background: radial-gradient(circle at 45% 40%, #b7bcc2, #7e868f);
  }
  .person { position: absolute; left: 22px; top: 232px; }
  .person-role { font-size: 11px; color: var(--accent-orange); }
  .person-name { font-size: 14px; font-weight: 600; margin-top: 2px; }
  .rule { position: absolute; left: 64px; right: 18px; height: 1.5px; background: var(--magenta); }
  .icon-column { position: absolute; left: 0; top: 296px; }
  .info { position: absolute; left: 66px; right: 18px; font-size: 11px; line-height: 15px; }
  .info-web { top: 303px; }
  .info-address { top: 352px; }
  .info-phones { top: 405px; line-height: 17px; }
  .info-phones li { list-style: none; display: flex; align-items: center; gap: 6px; }
  .info-phones svg { flex: none; }
</style>
</head>
<body>

<section class="card card-front" aria-label="Business card front">
  <div class="brand">
    <span class="brand-name">lumerova</span>
  </div>

  <svg class="contact-band" viewBox="0 0 525 44" aria-hidden="true">
    <defs>
      <linearGradient id="bandGrad" x1="0" x2="1">
        <stop offset="0" stop-color="#d0167f"/>
        <stop offset="1" stop-color="#a92a6e"/>
      </linearGradient>
    </defs>
    <rect width="525" height="44" fill="url(#bandGrad)"/>
    <g stroke="#fff" stroke-width="2">
      <line x1="40" y1="44" x2="56" y2="0"/>
      <line x1="96" y1="44" x2="112" y2="0"/>
      <line x1="278" y1="44" x2="294" y2="0"/>
      <line x1="328" y1="44" x2="344" y2="0"/>
    </g>
    <g transform="translate(76 22)" fill="none" stroke="#fff" stroke-width="1.6">
      <circle r="9"/>
      <ellipse rx="4" ry="9"/>
      <line x1="-9" y1="0" x2="9" y2="0"/>
      <line x1="-8" y1="-4.5" x2="8" y2="-4.5"/>
      <line x1="-8" y1="4.5" x2="8" y2="4.5"/>
    </g>
    <path transform="translate(303 12) scale(0.85)" fill="#fff"
      d="M4 0 L8 0 L10 6 L7 8 C8.5 11.5 11 14 14.5 15.5 L16.5 12.5 L22.5 14.5 L22.5 18.5 C22.5 20 21 22 19 22 C8.5 21 1 13.5 0 3 C0 1.2 2 0 4 0 Z"/>
  </svg>
  <span class="band-text band-web">www.lumerova.ch</span>
  <span class="band-text band-phone">+41 (0)21 480 13 57</span>
</section>

<section class="card card-back" aria-label="Business card back">
  <svg class="back-art" width="300" height="525" viewBox="0 0 300 525" aria-hidden="true">
    <defs>
      <linearGradient id="swoopGrad" x1="0" y1="0" x2="1" y2="1">
        <stop offset="0" stop-color="#a92a6e"/>
        <stop offset="1" stop-color="#cf157d"/>
      </linearGradient>
    </defs>
    <path fill="url(#swoopGrad)"
      d="M0 0 H300 V40 C240 46 215 90 200 140 C185 190 120 210 0 214 Z"/>
  </svg>

  <div class="back-brand">
    <span class="brand-name">lumerova</span>
  </div>

  <div class="portrait" role="img" aria-label="Portrait photo of the managing partner"></div>

  <div class="person">
    <p class="person-role">Managing partner</p>
    <p class="person-name">Name Surname, PhD</p>
  </div>

  <svg class="icon-column" width="56" height="208" viewBox="0 0 56 208" aria-hidden="true">
    <rect y="0" width="56" height="52" fill="#d0167f"/>
    <rect y="52" width="56" height="52" fill="#b5226f"/>
    <rect y="104" width="56" height="52" fill="#d81b84"/>
    <rect y="156" width="56" height="52" fill="#b8286f"/>
    <g transform="translate(28 26)" fill="none" stroke="#fff" stroke-width="1.8">
      <circle r="10"/>
      <ellipse rx="4.5" ry="10"/>
      <line x1="-10" y1="0" x2="10" y2="0"/>
      <line x1="-9" y1="-5" x2="9" y2="-5"/>
      <line x1="-9" y1="5" x2="9" y2="5"/>
    </g>
    <path transform="translate(28 78)" fill="#fff" fill-rule="evenodd"
      d="M0 11 C-5 4 -8 0 -8 -4 A8 8 0 0 1 8 -4 C8 0 5 4 0 11 Z M0 -7 A3 3 0 1 0 0.01 -7 Z"/>
    <path transform="translate(18 120)" fill="#fff"
      d="M4 0 L8 0 L10 6 L7 8 C8.5 11.5 11 14 14.5 15.5 L16.5 12.5 L22.5 14.5 L22.5 18.5 C22.5 20 21 22 19 22 C8.5 21 1 13.5 0 3 C0 1.2 2 0 4 0 Z"/>
    <g transform="translate(16 171)" fill="#fff">
      <rect x="5" y="0" width="14" height="6"/>
      <rect x="0" y="7" width="24" height="10" rx="1.5"/>
      <rect x="5" y="14" width="14" height="8" fill="#b8286f" stroke="#fff" stroke-width="1.6"/>
    </g>
  </svg>

  <div class="info info-web">
    <p>name@lumerova.ch</p>
    <p>www.lumerova.ch</p>
  </div>
  <div class="rule" style="top: 345px;"></div>
  <div class="info info-address">
    <p>Lumerova GmbH, Street</p>
    <p>name 1, 9999 City name</p>
    <p>Switzerland</p>
  </div>
  <div class="rule" style="top: 398px;"></div>
  <ul class="info info-phones">
    <li>
      <svg width="10" height="10" viewBox="0 0 10 10" aria-hidden="true"><path fill="#333" d="M0 10 V2 H4 V0 H10 V10 Z"/></svg>
      +41 (0)21 480 13 57
    </li>
    <li>
      <svg width="10" height="10" viewBox="0 0 23 22" aria-hidden="true"><path fill="#333" d="M4 0 L8 0 L10 6 L7 8 C8.5 11.5 11 14 14.5 15.5 L16.5 12.5 L22.5 14.5 L22.5 18.5 C22.5 20 21 22 19 22 C8.5 21 1 13.5 0 3 C0 1.2 2 0 4 0 Z"/></svg>
      +41 (0)21 480 13 60
    </li>
    <li>
      <svg width="10" height="10" viewBox="0 0 10 10" aria-hidden="true"><rect x="2" y="0" width="6" height="10" rx="1" fill="none" stroke="#333" stroke-width="1.4"/></svg>
      +41 (0)79 512 84 06
    </li>
    <li>
      <svg width="10" height="10" viewBox="0 0 10 10" aria-hidden="true"><path fill="#333" d="M2 0 H8 V3 H10 V8 H0 V3 H2 Z"/></svg>
      +41 (0)21 480 13 99
    </li>
  </ul>
</section>

</body>
</html>
```